Wagenhof Lindner

We need a web(graphic) design for an landing page on our internet portal providing a search engine to select a rental car. The search engine is using more as 150 rental car providers to find the best price. A comprehensive filter make the selection very quick and effective.
The design should be modern and clean. E.g. this website is what we have seen looks in our opinion good: http://wheels.quorbantrelpik.com

Reason: The decision takes a bit longer

Please change size to 960 px by 1500 px. Also please provide how many photoshop layers your design includes. Thank you.

Rental Car

```html
<!DOCTYPE html>
<html lang="en">
<head>
<meta charset="utf-8">
<title>Wagenhof Lindner – Rental Car Search</title>
<link href="https://fonts.googleapis.com/css2?family=Raleway:wght@400;500;600;700;800&display=swap" rel="stylesheet">
<style>
:root{
  --navy:#0f2565;
  --navy-deep:#0b1d52;
  --orange:#f7a00d;
  --orange-dark:#f08a00;
  --white:#ffffff;
  --text-muted:#a3a3a3;
  --label:#0f2565;
  --field-border:#dcdcdc;
  --field-text:#9a9a9a;
}
*{box-sizing:border-box;margin:0;padding:0}
html,body{width:1200px;height:1125px;overflow:hidden;background:var(--white)}
body{position:relative;font-family:"Raleway",sans-serif;color:var(--navy)}
.abs{position:absolute}

/* header */
.top-band{left:0;top:0;width:1200px;height:115px;background:var(--navy)}
.hero-bg{left:0;top:115px;width:1200px;height:460px;
  background:linear-gradient(180deg,#6f8fb8 0%,#a9b7c3 28%,#c9b39a 45%,#7c8d3c 62%,#9aa55a 72%,#e9ece4 88%,#ffffff 100%)}
.brand{left:240px;top:25px;display:flex;align-items:center;gap:8px}
.brand-mark{width:82px;height:44px;background:var(--white);border-radius:2px}
.brand-name{background:var(--orange);color:var(--white);font-weight:600;font-size:20px;padding:12px 12px;height:45px;line-height:21px;letter-spacing:.3px}
.phone{left:580px;top:36px;display:flex;align-items:center;gap:8px;color:var(--white);font-weight:600;font-size:18px}
.service{left:763px;top:39px;color:var(--white);font-size:12px;display:flex;align-items:center;gap:5px}
.lang{left:891px;top:35px;width:70px;height:24px;border-radius:12px;background:#0a1b4d;color:var(--white);font-size:11px;line-height:24px;padding-left:12px}
.lang::after{content:"";position:absolute;right:11px;top:10px;border:3px solid transparent;border-top:4px solid var(--white)}

/* nav */
.nav{left:240px;top:92px;width:720px;height:46px;background:var(--orange);border-radius:3px}
.nav a{position:absolute;top:0;line-height:46px;color:var(--white);text-decoration:none;font-size:14px;font-weight:500}
.nav .home{left:7px;top:8px;width:72px;height:30px;line-height:30px;text-align:center;background:var(--navy);border-radius:3px;font-weight:600}
.social{display:flex;gap:5px}
.social span{display:block;background:var(--white);border:2px solid var(--white);opacity:.9}
.nav .social{position:absolute;left:620px;top:10px}
.nav .social span{width:27px;height:26px;background:#eaeef7}

/* hero */
.person{left:100px;top:178px;width:126px;height:383px;background:linear-gradient(180deg,#e3b89a 0%,#d8a585 35%,#2d2d38 60%,#1e1e26 100%);border-radius:40px 6px 0 0}
.car{left:575px;top:320px;width:380px;height:205px;background:radial-gradient(ellipse at 50% 55%,#2a2d33 0%,#15171b 60%,rgba(20,20,24,0) 75%)}
.hero-title{left:589px;top:163px;color:var(--white);font-weight:800;text-shadow:0 1px 3px rgba(0,0,0,.25)}
.hero-title .small{display:block;font-size:26px;letter-spacing:.2px}
.hero-title .big{display:block;font-size:46px;line-height:52px;margin-top:2px}
.hero-copy{left:591px;top:249px;width:380px;color:var(--white);font-size:13px;line-height:19px;font-weight:500;text-shadow:0 1px 2px rgba(0,0,0,.3)}

/* search panel */
.panel{left:225px;top:153px;width:337px;height:417px;background:rgba(250,250,250,.97);box-shadow:0 0 4px rgba(0,0,0,.18)}
.panel h2{position:absolute;left:35px;color:var(--orange);font-size:18px;font-weight:700}
.panel label{position:absolute;font-size:11px;font-weight:700;color:var(--label)}
.field{position:absolute;height:28px;border:1px solid var(--field-border);background:var(--white);font-size:11px;color:var(--field-text);line-height:26px;padding-left:11px}
.field.select::after{content:"";position:absolute;right:12px;top:12px;border:3px solid transparent;border-top:4px solid var(--orange)}
.field .cal{position:absolute;right:8px;top:6px}
.check{position:absolute;left:38px;top:137px;font-size:11px;color:#555;display:flex;align-items:center;gap:7px}
.check span{width:10px;height:10px;border:1px solid #ccc;background:var(--white);position:relative}
.search-btn{position:absolute;left:38px;top:345px}

/* features */
.divider{left:487px;top:610px;width:226px;height:1px;background:#e6e6e6}
.dots{left:590px;top:607px;display:flex;gap:3px}
.dots i{display:block;width:5px;height:5px;border-radius:50%;background:#d8d8d8}
.feature h3{font-size:13px;font-weight:600;color:var(--navy);line-height:19px;display:flex;align-items:center;gap:5px}
.feature p{font-size:11px;line-height:19px;color:var(--text-muted);margin-top:7px}
.learn{color:var(--orange);font-size:11px;font-weight:600;display:flex;align-items:center;gap:6px;margin-top:10px}

/* signup */
.signup{left:240px;top:815px;width:720px;height:63px;background:var(--orange)}
.signup h4{position:absolute;left:25px;top:12px;color:var(--white);font-weight:500;font-size:18px;line-height:18px}
.signup h4 small{display:block;font-size:14px;line-height:16px}
.signup .email{position:absolute;left:322px;top:17px;width:268px;height:29px;background:var(--white);border:2px solid #f4c77a;font-size:12px;color:#999;line-height:25px;padding-left:10px}
.signup .send{position:absolute;right:4px;top:3px;width:55px;height:19px;background:var(--orange);color:var(--white);font-weight:700;font-size:12px;line-height:19px;text-align:center}
.signup .social{position:absolute;left:599px;top:16px;gap:6px}
.signup .social span{width:32px;height:29px;background:#eaeef7}

/* footer */
.footer{left:0;top:902px;width:1200px;height:190px;background:var(--navy)}
.fcol{position:absolute;top:14px}
.fcol h5{color:var(--white);font-size:15px;font-weight:700;margin-bottom:11px}
.fcol li{list-style:none;color:var(--white);font-size:11px;line-height:18.7px}
.support{position:absolute;left:772px;top:88px;width:188px;height:73px;background:var(--navy-deep);border:1px solid #1c3279;padding:10px 17px}
.support .lbl{color:var(--orange);font-size:9.5px;font-weight:500}
.support .num{color:var(--white);font-size:17px;font-weight:700;margin-top:5px}
.support .mail{color:var(--white);font-size:11px}
.copyright{left:0;top:1102px;width:1200px;text-align:center;font-size:11px;color:#a9a9a9}
</style>
</head>
<body>

<div class="abs top-band"></div>
<div class="abs hero-bg" role="img" aria-label="Landscape photo: cloudy sky with a rainbow over green fields"></div>

<header>
  <div class="abs brand">
    <span class="brand-mark"></span>
    <span class="brand-name">WAGENHOF LINDNER</span>
  </div>
  <div class="abs phone">
    <svg width="17" height="17" viewBox="0 0 24 24"><path fill="#f7a00d" d="M6.6 10.8a15.1 15.1 0 0 0 6.6 6.6l2.2-2.2c.3-.3.7-.4 1-.2 1.1.4 2.3.6 3.6.6.6 0 1 .4 1 1V20c0 .6-.4 1-1 1A17 17 0 0 1 3 4c0-.6.4-1 1-1h3.5c.6 0 1 .4 1 1 0 1.3.2 2.5.6 3.6.1.3 0 .7-.2 1z"/></svg>
    (555) 270-3190
  </div>
  <div class="abs service">
    <svg width="11" height="11" viewBox="0 0 12 12"><circle cx="6" cy="3.2" r="2.7" fill="#f7a00d"/><path d="M1 12c0-3 2.2-5 5-5s5 2 5 5z" fill="#f7a00d"/></svg>
    Customer Service
  </div>
  <div class="abs lang">English</div>

  <nav class="abs nav">
    <a class="home" href="#">Home</a>
    <a href="#" style="left:91px">About Us</a>
    <a href="#" style="left:178px">Trelvanta Faqs</a>
    <a href="#" style="left:305px">Help</a>
    <a href="#" style="left:365px">My Booking</a>
    <a href="#" style="left:467px">Support</a>
    <div class="social" aria-label="Social links"><span></span><span></span><span></span></div>
  </nav>
</header>

<section class="hero">
  <div class="abs person" role="img" aria-label="Photo of a smiling young man in a suit leaning out from behind the search panel"></div>
  <div class="abs car" role="img" aria-label="Photo of a black luxury saloon car"></div>
  <h1 class="abs hero-title"><span class="small">GREAT CAR HIRE DEALS</span><span class="big">NO HIDDEN FEES</span></h1>
  <p class="abs hero-copy">Phasellus eget ultricies libero.Sed dolor turpis,malesuada vitae cursus a, auctor semper neque.</p>

  <form class="abs panel">
    <h2 style="top:11px">WHERE?</h2>
    <label style="left:38px;top:36px">COUNTRY</label>
    <div class="field select" style="left:38px;top:52px;width:264px">Select your country</div>
    <label style="left:38px;top:87px">PICK-UP</label>
    <div class="field" style="left:38px;top:103px;width:264px">Type in Pickup City or Airport Code Here</div>
    <div class="check"><span><svg class="abs" style="left:1px;top:0" width="8" height="8" viewBox="0 0 8 8"><path d="M1 4l2 2 4-5" stroke="#f7a00d" stroke-width="1.4" fill="none"/></svg></span>Return to the same location</div>

    <h2 style="top:156px">WHEN?</h2>
    <label style="left:38px;top:182px">PICKUP ON</label>
    <label style="left:185px;top:182px">AT</label>
    <div class="field" style="left:38px;top:198px;width:135px">mm/dd/yyyy
      <svg class="cal" width="16" height="15" viewBox="0 0 16 15"><rect x="1" y="2" width="13" height="12" rx="1" fill="#f7a00d"/><rect x="3" y="6" width="9" height="6" fill="#fff"/><circle cx="12" cy="11" r="3.5" fill="#f08a00" stroke="#fff"/></svg></div>
    <div class="field select" style="left:185px;top:198px;width:117px">12:00AM</div>
    <label style="left:38px;top:234px">RETURN ON</label>
    <label style="left:185px;top:234px">AT</label>
    <div class="field" style="left:38px;top:250px;width:135px">mm/dd/yyyy
      <svg class="cal" width="16" height="15" viewBox="0 0 16 15"><rect x="1" y="2" width="13" height="12" rx="1" fill="#f7a00d"/><rect x="3" y="6" width="9" height="6" fill="#fff"/><circle cx="12" cy="11" r="3.5" fill="#f08a00" stroke="#fff"/></svg></div>
    <div class="field select" style="left:185px;top:250px;width:117px">12:00AM</div>
    <label style="left:38px;top:288px">I STAY IN</label>
    <label style="left:185px;top:288px">DRIVER AGE</label>
    <div class="field select" style="left:38px;top:305px;width:135px">Select Country</div>
    <div class="field select" style="left:185px;top:305px;width:117px">25+</div>

    <svg class="search-btn" width="264" height="45" viewBox="0 0 264 45">
      <path d="M0 0H264L250 22.5 264 45H0L14 22.5Z" fill="#f7a00d"/>
      <circle cx="85" cy="21" r="5" fill="none" stroke="#fff" stroke-width="2.2"/>
      <path d="M88.5 24.5l4 4" stroke="#fff" stroke-width="2.6" stroke-linecap="round"/>
      <text x="98" y="28" fill="#fff" font-family="Raleway, sans-serif" font-weight="700" font-size="16">SEARCH NOW</text>
    </svg>
  </form>
</section>

<div class="abs divider"></div>
<div class="abs dots"><i></i><i style="width:6px;height:6px"></i><i></i></div>

<section>
  <div class="abs feature" style="left:240px;top:637px;width:235px">
    <h3>We are leading car rental agency with 300,000 Happy Customers.</h3>
    <p>Morbi orci ante,consectetur id vestibulum quis,suscipit eu eros. Duis non egestas dolor.Duis non volutpat leo.Aliquam nisi eros,accumsan non gravida vitae,ultrices eu eros. Phasellus sagittis mattis tristique.</p>
    <div class="learn"><svg width="11" height="11" viewBox="0 0 12 12"><circle cx="6" cy="6" r="5" fill="none" stroke="#f7a00d" stroke-width="1.3"/><path d="M3.5 6h5" stroke="#f7a00d" stroke-width="1.3"/></svg>LEARN MORE</div>
  </div>
  <div class="abs feature" style="left:496px;top:637px;width:255px">
    <h3><svg width="11" height="11" viewBox="0 0 12 12"><path d="M6 0h6v6L6 12 0 6z" fill="#0f2565"/><circle cx="9" cy="3" r="1" fill="#fff"/></svg>Cheapest price guaranteed</h3>
    <p>Nunc ut nibh enim,id dapibus quam.Mauris id est at diam rutrum ultricies.Vivamus et dolor velit.Nam congue blandit nulla sed tincidunt.</p>
    <h3 style="margin-top:13px"><svg width="11" height="11" viewBox="0 0 12 12"><circle cx="6" cy="6" r="4" fill="none" stroke="#0f2565" stroke-width="2.5" stroke-dasharray="2 1.2"/><circle cx="6" cy="6" r="1.6" fill="#0f2565"/></svg>Dedicated customer support</h3>
    <p>Praesent tempus egestas blandit.Nunc euismod volutpat ultrices.</p>
  </div>
  <div class="abs feature" style="left:779px;top:637px;width:180px">
    <h3><svg width="11" height="11" viewBox="0 0 12 12"><path d="M1 1l9 4-4 1-1 4z" fill="#0f2565"/></svg>Zeero Booking Fees</h3>
    <p>Nunc ut nibh enim,id dapibus quam.Mauris id est at diam rutrum ultricies.Vivamus et dolor velit.Nam congue blandit nulla sed tincidunt. Morbi orci ante,consectetur id vestibulum quis,suscipit eu eros.</p>
  </div>
</section>

<section class="abs signup">
  <h4>SIGN UP FOR AMAZING OFFERS<small>exclusive access for offers and promotions</small></h4>
  <div class="email">Enter your email address<span class="send">SEND</span></div>
  <div class="social" aria-label="Social links"><span></span><span></span><span></span></div>
</section>

<footer class="abs footer">
  <div class="fcol" style="left:240px"><h5>EXTRA STUFF</h5><ul>
    <li>Site Map</li><li>Campervans</li><li>Price Promise</li><li>Blog</li><li>Meet the Lindner Team</li><li>Happy Customers</li><li>Why Us?</li></ul></div>
  <div class="fcol" style="left:392px"><h5>MORE COUNTRIES</h5><ul>
    <li>Scotland</li><li>Northern Ireland</li><li>Germany</li><li>Spain</li><li>France</li><li>Italy</li><li>Croatia</li></ul></div>
  <div class="fcol" style="left:566px"><h5>LEAVING EUROPE</h5><ul>
    <li>USA Car Rental</li><li>Canada Car Rental</li><li>Australia car rental</li><li>New Zealand Car Rental</li><li>Fiji Car Rental</li><li>Autovermietung Preisvergleich</li><li>Deutschland</li></ul></div>
  <div class="fcol" style="left:771px"><h5>FUN GUIDES &amp; TIPS</h5><ul>
    <li>Our Content Articles</li><li style="margin-top:3px">Location Guides</li></ul></div>
  <div class="support">
    <div class="lbl">ONLINE SUPPORT</div>
    <div class="num">(555) 270-3190</div>
    <div class="mail">sales@wagenhoflindner.com</div>
  </div>
</footer>

<p class="abs copyright">© Copyright Wagenhof Lindner 2014. All rights reserved</p>

</body>
</html>
```